Copperleaf Roofing Business Card

This is my current business card. But I’d like to make some changes. Somewhere on the card I’d like to list some of the services we offer. Maybe on the back? But I’d still like to keep the red. White and black modern look.

-residential & commercial roofing
-Roof Repairs & Maintenance
-Storm Damage & Insurance Claims specialist
-Christmas Lights and permanent Christmas lights
Fencing. Windows. Gutters. Siding. Sheetrock, painting.

```html
<!DOCTYPE html>
<html lang="en">
<head>
<meta charset="utf-8">
<title>Copperleaf Roofing Co. — Business Card</title>
<link href="https://fonts.googleapis.com/css2?family=Audiowide&family=Montserrat:wght@400;500&display=swap" rel="stylesheet">
<style>
  :root {
    --page: #d4d5d7;
    --red: #e0222a;
    --red-deep: #7a0f12;
    --black: #1b1b1b;
    --white: #ffffff;
    --grey-text: #e6e6e6;
  }
  * { margin: 0; padding: 0; box-sizing: border-box; }
  html, body { width: 900px; height: 1200px; overflow: hidden; }
  body {
    background: var(--page);
    font-family: "Montserrat", Arial, sans-serif;
    position: relative;
  }
  .card {
    position: absolute;
    left: 120px;
    width: 660px;
    height: 378px;
    border-radius: 16px;
    overflow: hidden;
  }
  .card-front { top: 204px; }
  .card-back { top: 620px; background: var(--black); }

  .tartan-fill {
    position: absolute; inset: 0;
    background: linear-gradient(160deg, var(--red-deep) 0%, var(--red) 45%, #9e1418 70%, #2a0a0b 100%);
  }
  .brand-mark {
    position: absolute;
    left: 50%;
    transform: translateX(-50%);
    border-radius: 50%;
    border: 3px solid var(--white);
  }
  .card-front .brand-mark { top: 73px; width: 150px; height: 150px; background: rgba(0,0,0,0.25); }
  .card-back .brand-mark { top: 25px; width: 120px; height: 120px; background: var(--red); border-color: var(--white); }

  .brand-name {
    position: absolute;
    left: 0; right: 0;
    text-align: center;
    font-family: "Audiowide", sans-serif;
    color: var(--white);
    letter-spacing: 1px;
    line-height: 1;
  }
  .card-front .brand-name { top: 246px; }
  .card-front .brand-name .line-1 { display: block; font-size: 38px; }
  .card-front .brand-name .line-2 { display: block; font-size: 27px; margin-top: 8px; }
  .card-back .brand-name { top: 160px; }
  .card-back .brand-name .line-1 { display: block; font-size: 30px; }
  .card-back .brand-name .line-2 { display: block; font-size: 21px; margin-top: 6px; }

  .services {
    position: absolute;
    right: 356px;
    top: 236px;
    list-style: none;
    text-align: right;
    color: var(--grey-text);
    font-size: 14px;
    line-height: 17px;
  }
  .services li { position: relative; padding-right: 14px; margin-bottom: 5px; }
  .services li::after {
    content: ""; position: absolute; right: 0; top: 6px;
    width: 5px; height: 5px; border-radius: 50%; background: var(--red);
  }
  .divider {
    position: absolute; left: 325px; top: 240px;
    width: 2px; height: 124px; background: var(--red);
  }
  .contact { position: absolute; left: 335px; top: 234px; color: var(--grey-text); }
  .person-name {
    font-family: "Audiowide", sans-serif;
    font-size: 25px; color: var(--white); letter-spacing: 1px; line-height: 1;
  }
  .person-name .surname { color: var(--red); }
  .person-role { font-size: 14px; margin-top: 6px; }
  .contact-list { list-style: none; margin-top: 10px; font-size: 14px; }
  .contact-list li { display: flex; align-items: center; gap: 8px; height: 24px; }
  .contact-list svg { width: 14px; height: 14px; fill: var(--red); flex: none; }

  .tartan-band {
    position: absolute; left: 0; right: 0; bottom: 0; height: 14px;
    background: linear-gradient(90deg, var(--red-deep), var(--red) 40%, var(--red-deep) 70%, var(--red));
  }
</style>
</head>
<body>
  <section class="card card-front">
    <div class="tartan-fill" role="img" aria-label="Red, black and white tartan pattern background"></div>
    <div class="brand-mark"></div>
    <h1 class="brand-name"><span class="line-1">COPPERLEAF</span><span class="line-2">ROOFING CO.</span></h1>
  </section>

  <section class="card card-back">
    <div class="brand-mark"></div>
    <h2 class="brand-name"><span class="line-1">COPPERLEAF</span><span class="line-2">ROOFING CO.</span></h2>

    <ul class="services">
      <li>residential &amp; commercial roofing</li>
      <li>Roof Repairs &amp; Maintenance</li>
      <li>Storm Damage &amp;<br>Insurance Claims specialist</li>
      <li>Fencing. Windows. Gutters.<br>Siding. Sheetrock, painting</li>
    </ul>

    <div class="divider"></div>

    <div class="contact">
      <p class="person-name">OWEN <span class="surname">CARRICK</span></p>
      <p class="person-role">Owner</p>
      <ul class="contact-list">
        <li><svg viewBox="0 0 24 24"><path d="M6.6 10.8a15.1 15.1 0 0 0 6.6 6.6l2.2-2.2c.3-.3.7-.4 1-.2 1.1.4 2.3.6 3.6.6.6 0 1 .4 1 1V20c0 .6-.4 1-1 1C10.6 21 3 13.4 3 4c0-.6.4-1 1-1h3.5c.6 0 1 .4 1 1 0 1.3.2 2.5.6 3.6.1.3 0 .7-.2 1z"/></svg>682-555-0148</li>
        <li><svg viewBox="0 0 24 24"><path d="M2 5h20v14H2z M2 5l10 7 10-7" /></svg>owen@copperleafroofing.com</li>
        <li><svg viewBox="0 0 24 24"><circle cx="12" cy="12" r="10"/></svg>www.copperleafroofing.com</li>
      </ul>
    </div>

    <div class="tartan-band" role="img" aria-label="Strip of red, black and white tartan pattern"></div>
  </section>
</body>
</html>
```